"Word Cloud" lists of countries, by decade, who have adopted women's suffrage

The winning designer will (eventually, but not necessarily within this project--see "Nice to Haves", below) design a total of eight images, based on the eight lists of countries (see attached files) in order, by decade, that they adopted women's suffrage.

One of the the attached images is a screen shot of five pages of the book RISE: The Argument for The Realm of Stars, showing how these lists are presently arranged on 6"x9" pages.

We essentially want to spice up these 8 lists and make them more fun to look at, for the reader.

Target Market(s)

General audience. People who want to make a difference. People who want to do something to change the world, and want to read a book about how we can actually do it.

Industry/Entity Type

Political

Font styles to use
Serif
Sans Serif
Decorative
Script

Requirements
Must have
• At least two initial designs, one for each of the two largest lists (lists 5 and 6). All country names must be spelled correctly. A WORD doc has been provided with all the text you need to work with. An EXAMPLE word cloud has been provided for inspiration. The look and feel of these "Country Clouds" wants to go all over the place, but all names should be (at least somewhat) readable.
• IMPORTANT ELEMENTS: (1) There are a few places where current countries were just one, when they got women's suffrage. Keep this info intact, together, in the cloud. EXAMPLE (from list 6):
•  British Leeward Islands (remove ", including today’s:", but keep together with)
•  Antigua and Barbuda
•  British Virgin Islands
•  Montserrat
•  Saint Kitts and Nevis
•  Anguilla
• (2) The names of the countries should stay in roughly the same order as found in the lists, but laid out (very) roughly right to left and then top to bottom, loosely akin to the standard flow of text written in the latin alphabet. It is fine to alter this standard in minor ways to achieve a better look to the design. Just don't move a country found at the top of one list into the middle of that list or down to the bottom, etc.
• These country clouds will be printed in black and white, so keep the designs greyscale.
• These "country clouds" should be 4.5" in width.The largest country clouds, with the most countries found in them, should not exceed 6" in length.
Nice to have
• (Eventually) all 8 lists in the form of "Country Clouds"---that are playful, but with serious elements. Pull up a list of countries by population, have the 20 biggest use the biggest font sizes. Use many different fonts, mix it up! Essentially, these 8 lists all want to become word clouds, with each nation's full name as its own "word." See example cloud.
• Though having all 8 lists in clouds at the end of this project is "nice to have," the winner for this design might simply produce 2 such clouds, along with a cost estimate attached to the submitted design for what they would charge to complete the other 6 clouds.
Should not have
• Do NOT include the textual transitions found between the lists, in the screen shot or word doc. They are there just to help you see how the different graphics will be used and what will go either before or after them.
• No need to use bullet points.

```html
<!DOCTYPE html>
<html lang="en">
<head>
<meta charset="utf-8">
<title>Country Cloud — Women's Suffrage by Decade</title>
<link rel="stylesheet" href="https://fonts.googleapis.com/css2?family=Cinzel&family=Cormorant+Garamond:wght@500&family=Raleway:wght@400;500&family=Montserrat:wght@400;500;600;700&family=Open+Sans:ital,wght@0,700;1,400&family=Roboto+Condensed:ital,wght@0,700;1,400;1,700&family=Archivo+Black&family=Arimo&family=Ubuntu:wght@500;700&family=Roboto+Mono:wght@700&family=Oswald:wght@400;700&family=Kaushan+Script&family=Rubik+Dirt&family=Alfa+Slab+One&family=Josefin+Sans:wght@700&family=Comfortaa:wght@300&family=Rubik:wght@400;700&family=Lobster&family=Pacifico&family=Patrick+Hand&family=Acme&family=Marcellus&family=Fredoka:wght@500&display=swap">
<style>
  :root {
    --paper: #ffffff;
    --ink: #2b2b2b;
    --ink-soft: #555555;
    --rule: #d4d4d4;
  }
  html, body { margin: 0; padding: 0; overflow: hidden; }
  body { background: var(--paper); }
  .cloud {
    position: relative;
    width: 800px;
    height: 1200px;
    background: var(--paper);
    color: var(--ink);
    overflow: hidden;
  }
  .country {
    position: absolute;
    line-height: 1;
    white-space: nowrap;
    margin: 0;
    transform-origin: left top;
  }
  .vertical { transform: rotate(-90deg); }
  .group-frame {
    position: absolute;
    border: 1px solid var(--rule);
    border-radius: 8px;
  }

  /* group frames */
  .frame-windward { left: 112px; top: 322px; width: 274px; height: 128px; }
  .frame-leeward  { left: 404px; top: 258px; width: 272px; height: 126px; border-right-color: transparent; }

  /* row 1 */
  .barbados { left: 108px; top: 268px; font: 400 50px "Cinzel", serif; letter-spacing: .05em; }

  /* British Windward Islands */
  .windward-1 { left: 110px; top: 331px; font: 500 42px "Raleway", sans-serif; transform: scaleX(.95); }
  .windward-2 { left: 110px; top: 374px; font: 500 28px "Raleway", sans-serif; transform: scaleX(.9); }
  .windward-3 { left: 109px; top: 405px; font: 500 38px "Raleway", sans-serif; transform: scaleX(.95); }
  .grenada { left: 266px; top: 323px; font: italic 400 24px "Open Sans", sans-serif; }
  .st-lucia { left: 269px; top: 352px; font: 400 18px "Archivo Black", sans-serif; }
  .st-vincent { left: 270px; top: 379px; font: 400 15px/17px "Arimo", sans-serif; }
  .dominica { left: 270px; top: 420px; font: 700 25px "Ubuntu", sans-serif; color: var(--ink-soft); }

  /* British Leeward Islands */
  .antigua { left: 413px; top: 267px; font: italic 400 14px "Open Sans", sans-serif; }
  .bvi { left: 412px; top: 284px; font: 400 15px "Raleway", sans-serif; }
  .montserrat { left: 411px; top: 301px; font: 600 22px "Montserrat", sans-serif; letter-spacing: .03em; color: var(--ink-soft); }
  .st-kitts { left: 412px; top: 329px; font: 700 16.5px "Roboto Condensed", sans-serif; }
  .anguilla { left: 413px; top: 356px; font: 500 16px "Montserrat", sans-serif; letter-spacing: .22em; color: var(--ink-soft); }
  .leeward { left: 566px; font: 700 32px "Open Sans", sans-serif; transform: scaleX(.85); }
  .leeward-1 { top: 272px; }
  .leeward-2 { top: 306px; }
  .leeward-3 { top: 340px; }

  /* right column block */
  .libya { left: 412px; top: 396px; font: 700 35px "Rubik", sans-serif; letter-spacing: .02em; }
  .nepal { left: 536px; top: 398px; font: 700 35px "Ubuntu", sans-serif; letter-spacing: .03em; }
  .cote { left: 410px; top: 433px; font: 700 31px "Roboto Mono", monospace; letter-spacing: .01em; }
  .lebanon { left: 668px; top: 502px; font: 700 24px "Oswald", sans-serif; letter-spacing: .06em; }

  /* middle block */
  .bhutan { left: 116px; top: 458px; font: 400 38px "Kaushan Script", cursive; }
  .guyana { left: 254px; top: 466px; font: 500 31px "Cormorant Garamond", serif; font-variant: small-caps; letter-spacing: .02em; }
  .mexico { left: 116px; top: 482px; font: 400 96px "Rubik Dirt", sans-serif; transform: scaleX(.62); }
  .belize { left: 374px; top: 578px; font: 400 26px "Alfa Slab One", serif; }
  .columbia { left: 414px; top: 476px; font: 700 25px "Josefin Sans", sans-serif; color: var(--ink-soft); }
  .ghana { left: 566px; top: 477px; font: 400 24px "Archivo Black", sans-serif; }
  .cambodia { left: 422px; top: 500px; font: 300 41px "Comfortaa", sans-serif; letter-spacing: .14em; color: var(--ink-soft); }
  .ethiopia { left: 418px; top: 542px; font: 400 40px "Oswald", sans-serif; letter-spacing: .06em; }
  .eritrea { left: 588px; top: 555px; font: italic 400 26px "Roboto Condensed", sans-serif; }

  /* row: Honduras */
  .honduras { left: 116px; top: 592px; font: 400 29px "Alfa Slab One", serif; letter-spacing: .02em; }
  .nicaragua { left: 320px; top: 597px; font: 700 21px "Rubik", sans-serif; }
  .peru { left: 444px; top: 586px; font: 400 40px "Lobster", cursive; }
  .benin { left: 530px; top: 598px; font: 400 23px "Raleway", sans-serif; letter-spacing: .03em; }
  .comoros { left: 610px; top: 598px; font: 400 24px "Lobster", cursive; }

  /* row: Egypt */
  .egypt { left: 116px; top: 628px; font: 500 82px "Cormorant Garamond", serif; }
  .gabon { left: 379px; top: 632px; font: 400 25px "Pacifico", cursive; }
  .mali { left: 465px; top: 638px; font: 400 32px "Raleway", sans-serif; }
  .mauritius { left: 538px; top: 630px; font: 400 40px "Lobster", cursive; }
  .somalia { left: 378px; top: 676px; font: 500 22px "Ubuntu", sans-serif; }
  .cayman { left: 474px; top: 678px; font: 400 21px "Montserrat", sans-serif; letter-spacing: .09em; }

  /* row: Malaysia */
  .malaysia { left: 118px; top: 706px; font: 400 46px "Patrick Hand", sans-serif; }
  .tunisia { left: 296px; top: 716px; font: 700 26px "Oswald", sans-serif; letter-spacing: .05em; }
  .burkina { left: 400px; top: 720px; font: 400 25.5px "Acme", sans-serif; }
  .chad { left: 572px; top: 753px; font: 700 20px "Oswald", sans-serif; }
  .guinea { left: 606px; top: 716px; font: 400 27px "Kaushan Script", cursive; }

  /* row: Laos */
  .laos { left: 118px; top: 759px; font: 700 26px "Ubuntu", sans-serif; }
  .brunei { left: 192px; top: 763px; font: 400 25px "Marcellus", serif; }
  .madagascar { left: 276px; top: 764px; font: 700 22px "Montserrat", sans-serif; letter-spacing: .02em; }
  .san-marino { left: 474px; top: 763px; font: 500 24px "Fredoka", sans-serif; }
  .tanzania { left: 602px; top: 764px; font: italic 700 24px "Roboto Condensed", sans-serif; }
</style>
</head>
<body>
<main class="cloud" aria-label="Countries that adopted women's suffrage in this decade">
  <p class="country barbados">BARBADOS</p>

  <section aria-label="British Windward Islands">
    <div class="group-frame frame-windward"></div>
    <p class="country windward-1">BRITISH</p>
    <p class="country windward-2">WINDWARD</p>
    <p class="country windward-3">ISLANDS</p>
    <p class="country grenada">Grenada</p>
    <p class="country st-lucia">ST. LUCIA</p>
    <p class="country st-vincent">St. Vincent and<br>the Grenadines</p>
    <p class="country dominica">Dominica</p>
  </section>

  <section aria-label="British Leeward Islands">
    <div class="group-frame frame-leeward"></div>
    <p class="country antigua">Antigua and Barbuda</p>
    <p class="country bvi">British Virgin Islands</p>
    <p class="country montserrat">Montserrat</p>
    <p class="country st-kitts">Saint Kitts and Nevis</p>
    <p class="country anguilla">ANGUILLA</p>
    <p class="country leeward leeward-1">BRITISH</p>
    <p class="country leeward leeward-2">LEEWARD</p>
    <p class="country leeward leeward-3">ISLANDS</p>
  </section>

  <p class="country libya">Libya</p>
  <p class="country nepal">NEPAL</p>
  <p class="country cote">Côte d’Ivoire</p>
  <p class="country lebanon vertical">LEBANON</p>

  <p class="country bhutan">Bhutan</p>
  <p class="country guyana">Guyana</p>
  <p class="country mexico">MEXICO</p>
  <p class="country belize vertical">BELIZE</p>
  <p class="country columbia">COLUMBIA</p>
  <p class="country ghana">GHANA</p>
  <p class="country cambodia">cambodia</p>
  <p class="country ethiopia">ETHIOPIA</p>
  <p class="country eritrea">ERITREA</p>

  <p class="country honduras">HONDURAS</p>
  <p class="country nicaragua">Nicaragua</p>
  <p class="country peru">Peru</p>
  <p class="country benin">BENIN</p>
  <p class="country comoros">Comoros</p>

  <p class="country egypt">EGYPT</p>
  <p class="country gabon">Gabon</p>
  <p class="country mali">mali</p>
  <p class="country mauritius">Mauritius</p>
  <p class="country somalia">Somalia</p>
  <p class="country cayman">CAYMAN ISLANDS</p>

  <p class="country malaysia">MALAYSIA</p>
  <p class="country tunisia">TUNISIA</p>
  <p class="country burkina">BURKINA FASO</p>
  <p class="country chad vertical">CHAD</p>
  <p class="country guinea">Guinea</p>

  <p class="country laos">Laos</p>
  <p class="country brunei">Brunei</p>
  <p class="country madagascar">MADAGASCAR</p>
  <p class="country san-marino">San Marino</p>
  <p class="country tanzania">Tanzania</p>
</main>
</body>
</html>
```